New Business Card Design Project

I need a design for business cards, i am an electrical business called "Corvane Electrical and Communications" i need the cards to be double sided with the company logo on the back (attached) the front needs to say my company name, web site, email address, telephone number, and ABN number and electrical license number. I am open to different arrangements of the information but would like the background to be incorporating something electrical or something that looks smart. open to all additional ideas also.

The company colours are orange and grey see logo attached.

Business Name: Corvane Electrical and Communications
Website: corvaneelectricalandcomms.example.com.au
Email: brent@corvaneelectricalandcomms.example.com.au
Telephone(mobile): 0481209736
ABN: 71208349162
Lic No: 418273D

Target Market(s)

Business entities, Project Managers, Accounts, Clients

Industry/Entity Type

Electrician

Contact Information for Business Card

I need a design for business cards, i am an electrical business called "Corvane Electrical and Communications" i need the cards to be double sided with the company logo on the back (attached) the front needs to say my company name

Font styles to use
Serif
Sans Serif

Colors
f37122
5c5c5c

Requirements
Must have
• Must have the Logo on the back open to different ways of it being on the back but had in mind to keep it central but again open to other options
Nice to have
• A real modern cool background that is eye catching yet contemporary
Should not have
• No backgrounds of a light bulb or plug or anything like that

```html
<!DOCTYPE html>
<html lang="en">
<head>
<meta charset="utf-8">
<title>Corvane Electrical and Communications – Business Card</title>
<link href="https://fonts.googleapis.com/css2?family=Arimo:wght@400&family=Open+Sans:wght@400&display=swap" rel="stylesheet">
<style>
  :root {
    --backdrop: #8f8f90;
    --card-grey: #48484c;
    --brand-orange: #d9921a;
    --text-light: #eeeeef;
    --text-dark: #3e3e42;
  }
  * { margin: 0; padding: 0; box-sizing: border-box; }
  html, body {
    width: 1105px;
    height: 1200px;
    overflow: hidden;
    background: var(--backdrop);
  }
  .canvas {
    position: relative;
    width: 1105px;
    height: 1200px;
  }
  .card {
    position: absolute;
    left: 182px;
    width: 747px;
    height: 427px;
    background: var(--card-grey);
    overflow: hidden;
  }
  .card--front { top: 119px; }
  .card--back  { top: 637px; }

  .front__band {
    position: absolute;
    left: 0;
    top: 0;
    width: 747px;
    height: 170px;
    background: linear-gradient(180deg, var(--brand-orange) 0%, var(--brand-orange) 55%, var(--card-grey) 100%);
  }
  .holder {
    position: absolute;
    left: 35px;
    top: 36px;
    font-family: "Arimo", Arial, sans-serif;
    color: var(--text-dark);
  }
  .holder__name {
    font-size: 27px;
    font-weight: 400;
    letter-spacing: 0.5px;
    line-height: 1;
  }
  .holder__role {
    margin-top: 10px;
    font-size: 18px;
    font-weight: 400;
    line-height: 1;
  }
  .company-name {
    position: absolute;
    left: 52px;
    top: 268px;
    display: flex;
    align-items: center;
    gap: 14px;
  }
  .company-name__dot {
    width: 18px;
    height: 18px;
    border-radius: 50%;
    background: var(--brand-orange);
    flex: none;
  }
  .company-name__text {
    font-family: "Arimo", Arial, sans-serif;
    font-weight: 400;
    font-size: 26px;
    line-height: 1.25;
    color: var(--text-light);
  }
  .details {
    position: absolute;
    left: 370px;
    top: 244px;
    font-family: "Arimo", Arial, sans-serif;
    color: var(--text-light);
    list-style: none;
  }
  .details__item {
    display: flex;
    align-items: center;
    height: 29px;
    font-size: 19px;
    white-space: nowrap;
  }
  .details__item--small { font-size: 13.5px; }
  .details__item--gap { margin-top: 4px; }
  .details__icon {
    width: 16px;
    height: 16px;
    margin-right: 8px;
    flex: none;
  }

  .back__name {
    position: absolute;
    left: 0;
    top: 206px;
    width: 100%;
    text-align: center;
    font-family: "Arimo", Arial, sans-serif;
    font-weight: 400;
    font-size: 30px;
    color: var(--brand-orange);
  }
  .back__web {
    position: absolute;
    left: 0;
    top: 338px;
    width: 100%;
    text-align: center;
    font-family: "Open Sans", Arial, sans-serif;
    font-size: 18px;
    letter-spacing: 1px;
    color: var(--text-light);
  }
</style>
</head>
<body>
<main class="canvas">

  <section class="card card--front" aria-label="Card front">
    <div class="front__band" role="img" aria-label="Orange header band with a white cable forming a wave across the card"></div>

    <div class="holder">
      <p class="holder__name">DANA WHITLOCK</p>
      <p class="holder__role">CEO/FOUNDER</p>
    </div>

    <div class="company-name">
      <span class="company-name__dot"></span>
      <p class="company-name__text">Corvane Electrical<br>&amp; Communications</p>
    </div>

    <ul class="details">
      <li class="details__item">ABN: 71208349162</li>
      <li class="details__item">Lic No: 418273D</li>
      <li class="details__item details__item--gap">
        <svg class="details__icon" viewBox="0 0 16 16" aria-hidden="true">
          <rect x="4" y="1" width="8" height="14" rx="1.5" fill="none" stroke="var(--brand-orange)" stroke-width="1.8"/>
          <circle cx="8" cy="12.3" r="0.9" fill="var(--brand-orange)"/>
        </svg>0481209736
      </li>
      <li class="details__item details__item--small">
        <svg class="details__icon" viewBox="0 0 16 16" aria-hidden="true">
          <rect x="1" y="3" width="14" height="10" fill="var(--brand-orange)"/>
          <path d="M1 3 L8 9 L15 3" fill="none" stroke="var(--card-grey)" stroke-width="1.3"/>
        </svg>brent@corvaneelectricalandcomms.example.com.au
      </li>
      <li class="details__item details__item--small">
        <svg class="details__icon" viewBox="0 0 16 16" aria-hidden="true">
          <circle cx="8" cy="8" r="7" fill="var(--brand-orange)"/>
          <path d="M1 8 H15 M8 1 C4 5 4 11 8 15 M8 1 C12 5 12 11 8 15" fill="none" stroke="var(--card-grey)" stroke-width="1"/>
        </svg>corvaneelectricalandcomms.example.com.au
      </li>
    </ul>
  </section>

  <section class="card card--back" aria-label="Card back">
    <p class="back__name">Corvane Electrical and Communications</p>
    <p class="back__web">www.corvaneelectricalandcomms.example.com.au</p>
  </section>

</main>
</body>
</html>
```